Background on the company
=======================
This is a Bitcoin Consulting Company.

We have two projects.

Painted Tokens: software to trade assets over the Bitcoin protocol (assets like property, traditional currencies, gold, stocks, securities, bonds, etc.).

Vaultfern Home Steward: a hardware based web service in a box that manages cold storage wallets and off line transaction signing. It is the secure way to deploy a web wallet without relying on third parties.

All that to say this is a high tech company focusing on Bitcoin.

What does Wyndolmere mean?
========================

The Terror of Wyndolmere is the rabbit in Pelham Gristle's Silver Chalice that defeats his band of knights. (At least until they go and get the Sacred Brass Catapult).

We like this, because we are a deceptively soft and fuzzy company that is also killer!

What We Need:
============

Primarily we need to get the logo designed. I have a hand drawing I did, but you are not limited to that. And the logo needs to work on a business card. The right logo that works on a Business Card is the primary consideration.

The main task here is to get the logo right.  I have provided a drawing I made, and I like it, but my complaints are:  Wyndolmere is hard to read.  The 'C' isn't obvious.

We can fix this many ways.  We can forget the whole "combinde a rabit with the C and a" idea.  We can add "Wyndolmere Systems" on the card apart from the logo (that way if they don't "get it" they can still read it.)

The Rabbit itself is quite obviously scanned from a hand drawing.  That might not be a bad thing, but combine that with the entire logo, and it is too cheap looking.

Target Market(s)

Technical folks. Investors. Business contacts.

Industry/Entity Type

Software

Requirements
Must have
• We have to clean up the logo, or replace it with something that hints at the same sort of things. (See the upload) Basically and innocent white bunny. Something that works on a Business Card.

All the information below:

Derek Vale
ph (555) 314-9027
vale.derek@mailorbit.example
derek@wyndolmere.example
Nice to have
• I would like it to be serious, yet whimsical. An inside joke, so you get it if you know Pelham Gristle. But otherwise, it looks reasonably serious if you don't know Pelham Gristle.

I don't want it to be scary. (oddly, that my own efforts seem to make that easy to do)

Would like a set of colors that remind one of a cave, a rabbit, knights.... Not sure what those are...

```html
<!DOCTYPE html>
<html lang="en">
<head>
<meta charset="utf-8">
<title>Wyndolmere Systems – Business Card</title>
<link rel="stylesheet" href="https://fonts.googleapis.com/css2?family=Open+Sans:wght@400;700&display=swap">
<style>
  :root {
    --page-bg: #e4e4e2;
    --card-bg: #ffffff;
    --card-shadow: rgba(0, 0, 0, 0.18);
    --brand-red: #c8161d;
    --ink-grey: #6f6f6f;
    --ink-dark: #585858;
    --art-dark: #1e1e1e;
    --art-mid: #3a3a3a;
  }
  * { box-sizing: border-box; margin: 0; padding: 0; }
  html, body {
    width: 1200px;
    height: 900px;
    overflow: hidden;
    background: var(--page-bg);
    font-family: "Open Sans", Arial, sans-serif;
  }
  .canvas {
    width: 1200px;
    height: 900px;
    display: flex;
    align-items: center;
    justify-content: center;
  }
  .business-card {
    position: relative;
    width: 1000px;
    height: 572px;
    background: var(--card-bg);
    border-radius: 44px;
    box-shadow: 0 14px 40px var(--card-shadow);
  }
  .brand-block {
    position: absolute;
    top: 104px;
    left: 0;
    right: 0;
    display: flex;
    flex-direction: column;
    align-items: center;
  }
  .mascot-art {
    width: 240px;
    height: 160px;
    border-radius: 46% 46% 10% 10%;
    background: radial-gradient(ellipse at 50% 40%, var(--art-mid) 0%, var(--art-dark) 70%);
  }
  .brand-name {
    margin-top: 14px;
    font-weight: 700;
    font-size: 24px;
    letter-spacing: -0.3px;
    color: var(--brand-red);
    text-transform: lowercase;
    white-space: nowrap;
  }
  .contact-row {
    position: absolute;
    left: 0;
    right: 0;
    bottom: 84px;
    display: flex;
    justify-content: center;
    align-items: center;
    gap: 28px;
    font-size: 18px;
    color: var(--ink-grey);
    white-space: nowrap;
  }
  .contact-name {
    font-weight: 700;
    color: var(--ink-dark);
  }
  .contact-item {
    display: flex;
    align-items: center;
    gap: 7px;
  }
  .contact-icon {
    width: 18px;
    height: 18px;
    fill: var(--ink-dark);
  }
</style>
</head>
<body>
<main class="canvas">
  <section class="business-card">
    <div class="brand-block">
      <div class="mascot-art" role="img" aria-label="Dark company mascot illustration"></div>
      <div class="brand-name">Wyndolmere Systems</div>
    </div>
    <div class="contact-row">
      <span class="contact-name">Derek Vale</span>
      <span class="contact-item">
        <svg class="contact-icon" viewBox="0 0 24 24" aria-hidden="true">
          <path d="M6.6 10.8a15.1 15.1 0 0 0 6.6 6.6l2.2-2.2a1 1 0 0 1 1-.25 11.4 11.4 0 0 0 3.6.57 1 1 0 0 1 1 1V20a1 1 0 0 1-1 1A17 17 0 0 1 3 4a1 1 0 0 1 1-1h3.5a1 1 0 0 1 1 1c0 1.25.2 2.45.57 3.6a1 1 0 0 1-.25 1z"/>
        </svg>
        (555) 314-9027
      </span>
      <span class="contact-item">
        <svg class="contact-icon" viewBox="0 0 24 24" aria-hidden="true">
          <path d="M2 5h20v14H2z M3.5 6.5 12 13l8.5-6.5" fill="none" stroke="#585858" stroke-width="2"/>
          <path d="M2 5h20L12 13z"/>
        </svg>
        vale.derek@mailorbit.example
      </span>
      <span class="contact-item">derek@wyndolmere.example</span>
    </div>
  </section>
</main>
</body>
</html>
```